Design a product reviews website

We need a website design and simple logo for the brand Venlotix.com. The website will provide reviews of technology products and services. The brand and website should be approachable but should also be trustworthy and high quality. The deliverable should be designs, specs and assets that I can provide to a development team to build the website.

Target Market(s)

People researching products to buy.

Industry/Entity Type

Product

Logo Text

Venlotix.com

Number of Pages Required

5+ page

Font styles to use
Sans Serif

Colors
0492cd
0355a3
3176b5
33a6d7
85cae6
85abd2
cedeed
cee9f5

Requirements
Must have
• - Designs for the Homepage, Category and Article pages.
• - Designs for web and mobile.
• - Designs details for the engineering team to use for development.
• - I'm open to other colors than the preferences I chose but I'm more likely to like blues, greys and blacks.

```html
<!DOCTYPE html>
<html lang="en">
<head>
<meta charset="utf-8">
<title>Venlotix.com — Product Reviews</title>
<link rel="stylesheet" href="https://fonts.googleapis.com/css2?family=Bitter:ital,wght@0,400;0,700;1,400&family=Montserrat:wght@600;700&display=swap">
<style>
:root{
  --navy:#0355a3;
  --blue:#3176b5;
  --sky:#33a6d7;
  --bright:#0492cd;
  --ink:#222;
  --text:#444;
  --muted:#666;
  --page:#f4f4f4;
  --line:#dcdcdc;
  --star:#f39c12;
  --star-off:#999;
  --footer:#232323;
  --footer-deep:#151515;
  --white:#fff;
}
*{box-sizing:border-box;margin:0;padding:0}
html,body{width:1200px;height:2985px;overflow:hidden}
body{font-family:"Bitter",Georgia,serif;color:var(--text);background:var(--page);position:relative}
.abs{position:absolute}

/* header */
.site-header{left:0;top:0;width:1200px;height:76px;background:var(--white)}
.brand{left:86px;top:20px;font:700 26px/36px "Bitter",serif;color:var(--navy);letter-spacing:.5px}
.search{left:844px;top:20px;width:216px;height:36px;border:1px solid #aac;border-radius:4px;font-size:12px;color:#333;padding:10px 12px}
.search svg{position:absolute;right:8px;top:8px}
.menu-btn{left:1080px;top:20px;width:38px;height:38px;background:var(--navy);border-radius:4px}
.menu-btn i{position:absolute;left:11px;width:16px;height:2px;background:#fff}

/* hero */
.hero{left:0;top:76px;width:1200px;height:612px;background:linear-gradient(100deg,#cfd3d6 0%,#9a9c9c 30%,#5a5a5c 50%,#8e8a84 70%,#c2bcb3 100%)}
.hero-floor{left:0;top:520px;width:1200px;height:168px;background:linear-gradient(180deg,#8a5a34,#b07a4a)}
.hero-band{left:0;top:290px;width:432px;height:172px;background:rgba(30,30,30,.72)}
.hero-kicker{left:86px;top:322px;font:700 20px/24px "Montserrat",sans-serif;color:#fff}
.hero-title{left:86px;top:356px;font:700 29px/38px "Montserrat",sans-serif;color:#fff}
.dot{top:574px;width:24px;height:24px;border:3px solid #fff;border-radius:50%}
.dot.on{background:var(--sky)}

/* sidebar */
.side-nav{left:72px;top:730px;width:264px;list-style:none}
.side-nav li{height:54px;background:var(--blue);border-bottom:1px solid #5a93c8;color:#fff;font-size:15px;display:flex;align-items:center;padding-left:44px;position:relative}
.side-nav li.active{background:var(--navy)}
.side-nav li::before{content:"";position:absolute;left:16px;top:20px;width:14px;height:12px;border:2px solid #b8d3ec;border-radius:2px}
.side-nav li::after{content:"";position:absolute;right:18px;top:22px;width:8px;height:8px;border-top:2px solid #fff;border-right:2px solid #fff;transform:rotate(45deg)}

/* panels */
.panel-head{height:52px;background:var(--navy);color:#fff;font-size:16px;line-height:52px;padding-left:18px}
.card{background:#fff;border:1px solid var(--line)}
.photo{width:100%}
.stars{color:var(--star);font-size:20px;letter-spacing:3px}
.stars .off{color:var(--star-off)}
.card h3{font-weight:400;font-size:19px;color:var(--ink)}
.card p{font-size:13px;line-height:22px;color:var(--text)}
.meta-bar{position:absolute;left:0;bottom:0;width:100%;height:40px;background:var(--sky);color:#fff;font-size:12px;font-style:italic;display:flex;align-items:center;gap:22px;padding-left:14px}
.meta-bar u{font-style:italic}
.meta-bar .go{position:absolute;right:0;top:0;width:40px;height:40px;background:var(--blue)}
.go::after{content:"";position:absolute;left:13px;top:15px;width:9px;height:9px;border-top:2px solid #fff;border-right:2px solid #fff;transform:rotate(45deg)}
.avatar{width:24px;height:24px;border-radius:50%;background:#dfe6ee;border:2px solid #fff}
.loading{left:362px;top:1964px;width:488px;height:40px;border:1px solid #bbb;border-radius:4px;background:#fff;font-size:13px;font-style:italic;text-align:center;line-height:38px;color:#333}

.pop .photo{height:176px}
.pop h4{position:absolute;left:18px;top:192px;font-weight:400;font-size:17px;color:var(--ink)}
.pop .cat{position:absolute;left:18px;top:222px;font-size:12px;font-style:italic;color:#555}
.pop .go{position:absolute;right:18px;top:196px;width:40px;height:40px;background:var(--blue)}
.pop .rate{position:absolute;left:16px;top:136px;background:rgba(60,60,60,.75);padding:2px 8px;font-size:20px;letter-spacing:3px;color:var(--star)}

/* about */
.about{left:0;top:2050px;width:1200px;height:444px;background:linear-gradient(180deg,#3b7fbd,#2f72b1)}
.about h2{position:absolute;left:0;width:1200px;top:110px;text-align:center;font-weight:400;font-size:40px;color:#fff;letter-spacing:1px}
.about .rule{position:absolute;left:540px;top:170px;width:120px;height:1px;background:#8fb5de}
.about p{position:absolute;left:200px;width:800px;top:196px;text-align:center;color:#fff;font-weight:700;font-size:14px;line-height:28px}

/* footer */
.footer{left:0;top:2494px;width:1200px;height:456px;background:var(--footer);color:#fff}
.news{left:84px;top:50px;width:666px;height:70px;border:1px solid #777;border-radius:4px}
.news span{position:absolute;left:54px;top:20px;font-size:19px}
.news .field{position:absolute;left:240px;top:16px;width:360px;height:38px;background:#fff;color:#222;font-size:13px;padding:11px 12px}
.news .sub{position:absolute;left:600px;top:16px;width:104px;height:38px;background:var(--sky);font:700 13px/38px "Bitter",serif;text-align:center;letter-spacing:.5px}
.follow{left:842px;top:72px;font-size:19px}
.social{top:66px;width:34px;height:34px;border:2px solid #fff;border-radius:50%;background:var(--navy)}
.f-title{font-size:22px}
.f-rule{height:1px;background:#555}
.input{border:1px solid #888;font-size:13px;padding:0 12px;line-height:38px;height:40px}
.submit{background:var(--sky);font:700 15px/40px "Bitter",serif;text-align:center;letter-spacing:1px}
.links{list-style:none;font-size:14px;line-height:27px}
.links li::before{content:"›";margin-right:10px}
.vline{width:1px;background:#555}
.contact{font-size:13px;line-height:22px}
.bottom{left:0;top:2950px;width:1200px;height:35px;background:var(--footer-deep);border-top:6px solid var(--navy);color:#fff;font-size:13px;text-align:center;line-height:29px}
.top-tab{left:584px;top:2936px;width:32px;height:14px;background:var(--navy);clip-path:polygon(20% 0,80% 0,100% 100%,0 100%)}
</style>
</head>
<body>

<header class="abs site-header">
  <div class="abs brand">VENLOTIX</div>
  <div class="abs search">Search Here
    <svg width="18" height="18" viewBox="0 0 18 18"><circle cx="7.5" cy="7.5" r="5.5" fill="none" stroke="#3176b5" stroke-width="2"/><path d="M11.5 11.5l5 5" stroke="#3176b5" stroke-width="2"/></svg>
  </div>
  <div class="abs menu-btn"><i style="top:13px"></i><i style="top:18px"></i><i style="top:23px"></i></div>
</header>

<section class="abs hero" role="img" aria-label="Room with home appliances and electronics: fridge, speakers, microwave, washer, TV and laptop"></section>
<div class="abs hero-floor" role="img" aria-label="Wooden floor of the appliance room"></div>
<div class="abs hero-band"></div>
<div class="abs hero-kicker">KNOW BEST DEAL ON</div>
<div class="abs hero-title">HOME APPLIANCES &amp;<br>ELECTRONIC GADGETS</div>
<div class="abs dot on" style="left:544px"></div>
<div class="abs dot" style="left:590px"></div>
<div class="abs dot" style="left:636px"></div>

<ul class="abs side-nav">
  <li class="active">Home</li>
  <li>Appliances</li>
  <li>Computers</li>
  <li>Electronics</li>
  <li>Home Security</li>
  <li>Mobile</li>
  <li>Smart Home</li>
  <li>Software</li>
</ul>

<!-- latest products -->
<div class="abs panel-head" style="left:362px;top:730px;width:488px">LATEST PRODUCTS</div>

<article class="abs card" style="left:362px;top:792px;width:488px;height:368px">
  <div class="photo" style="height:176px;background:linear-gradient(180deg,#e4e4e4,#f3f3f3)" role="img" aria-label="Speaker set with subwoofer"></div>
  <div class="abs stars" style="left:20px;top:188px">★★★★<span class="off">★</span></div>
  <h3 class="abs" style="left:20px;top:228px">The Aura Voice Hub</h3>
  <p class="abs" style="left:20px;top:258px;width:450px">Lorem ipsum dolor sit amet, consectetuer adipiscing elit, sed diam nonummy nibh euismod tincidunt ut laoreet dolore magna</p>
  <div class="meta-bar"><span class="avatar"></span><span>By John</span><span>On 11/08/2016</span><span>In <u>Home</u>, <u>Speakers</u></span><span class="go"></span></div>
</article>

<article class="abs card" style="left:362px;top:1186px;width:236px;height:364px">
  <div class="photo" style="height:176px;background:linear-gradient(135deg,#6f6f6f,#d9d9d9)" role="img" aria-label="Built-in kitchen appliances"></div>
  <div class="abs stars" style="left:18px;top:188px">★★★★<span class="off">★</span></div>
  <h3 class="abs" style="left:18px;top:226px;font-size:17px">Kitchen Appliances</h3>
  <p class="abs" style="left:18px;top:254px;width:210px">Lorem ipsum dolor sit amet, consectetuer adipiscing elit</p>
  <div class="meta-bar"><span>In <u>Home</u>, <u>Kitchen</u></span><span class="go"></span></div>
</article>

<article class="abs card" style="left:616px;top:1186px;width:234px;height:364px">
  <div class="photo" style="height:176px;background:linear-gradient(135deg,#5a3a26,#a9876a)" role="img" aria-label="Juicer mixer grinder on a counter"></div>
  <div class="abs stars" style="left:18px;top:188px">★★★★<span class="off">★</span></div>
  <h3 class="abs" style="left:18px;top:226px;font-size:17px">Juicer Mixer Grinder</h3>
  <p class="abs" style="left:18px;top:254px;width:210px">Lorem ipsum dolor sit amet, consectetuer adipiscing elit</p>
  <div class="meta-bar"><span>In <u>Home</u>, <u>Kitchen</u></span><span class="go"></span></div>
</article>

<article class="abs card" style="left:362px;top:1568px;width:488px;height:372px">
  <div class="photo" style="height:176px;background:linear-gradient(180deg,#e6e2dc 0,#fff 22px)" role="img" aria-label="Home theater system"></div>
  <div class="abs stars" style="left:20px;top:192px">★★★★<span class="off">★</span></div>
  <h3 class="abs" style="left:20px;top:232px">Home Theater</h3>
  <p class="abs" style="left:20px;top:262px;width:450px">Lorem ipsum dolor sit amet, consectetuer adipiscing elit, sed diam nonummy nibh euismod tincidunt ut laoreet dolore magna</p>
  <div class="meta-bar"><span class="avatar"></span><span>By John</span><span>On 11/08/2016</span><span>In <u>Home</u>, <u>Electronics</u></span><span class="go"></span></div>
</article>

<div class="abs loading">◌ &nbsp;Loading</div>

<!-- popular products -->
<div class="abs panel-head" style="left:876px;top:730px;width:258px">POPULAR PRODUCTS</div>

<article class="abs card pop" style="left:876px;top:792px;width:258px;height:256px">
  <div class="photo" style="background:linear-gradient(135deg,#8a8d90,#b4652e 50%,#7a4a2a)" role="img" aria-label="Copper pots hanging on a tiled wall"></div>
  <div class="rate">★★★★<span style="color:var(--star-off)">★</span></div>
  <h4>Copper Pots</h4><div class="cat">In <u>Home</u>, <u>Utensils</u></div><span class="go"></span>
</article>
<article class="abs card pop" style="left:876px;top:1072px;width:258px;height:256px">
  <div class="photo" style="background:linear-gradient(180deg,#2a2a2a,#0e0e0e)" role="img" aria-label="Wireless speakers on black background"></div>
  <div class="rate" style="background:none">★★★<span style="color:var(--star-off)">★</span></div>
  <h4>Wireless Speakers</h4><div class="cat">In <u>Home</u>, <u>Speakers</u></div><span class="go"></span>
</article>
<article class="abs card pop" style="left:876px;top:1352px;width:258px;height:256px">
  <div class="photo" style="background:linear-gradient(180deg,#f0f0f0,#d8dce0)" role="img" aria-label="Electrical steam iron"></div>
  <div class="rate">★★★½<span style="color:var(--star-off)">★</span></div>
  <h4>Electrical Iron</h4><div class="cat">In <u>Home</u>, <u>Utensils</u></div><span class="go"></span>
</article>
<article class="abs card pop" style="left:876px;top:1630px;width:258px;height:256px">
  <div class="photo" style="background:linear-gradient(135deg,#8a8d90,#b4652e 50%,#7a4a2a)" role="img" aria-label="Copper pots hanging on a tiled wall"></div>
  <div class="rate">★★★★<span style="color:var(--star-off)">★</span></div>
  <h4>Copper Pots</h4><div class="cat">In <u>Home</u>, <u>Utensils</u></div><span class="go"></span>
</article>

<!-- about -->
<section class="abs about" role="img" aria-label="Faint backdrop of home appliances and electronics in blue">
  <h2>ABOUT VENLOTIX</h2>
  <div class="rule"></div>
  <p>Lorem ipsum dolor sit amet, consectetuer adipiscing elit, sed diam nonummy nibh euismod tincidunt ut laoreet dolore magna aliquam erat volutpat. Ut wisi enim ad minim veniam, quis nostrud exerci tation ullamcorper suscipit lobortis nisl ut aliquip ex ea commodo consequat. Duis autem vel eum iriure dolor in hendrerit in vulputate velit esse molestie consequat, vel illum dolore eu feugiat nulla facilisis at vero eros et accumsan et iusto odio dignissim qui blandit praesent luptatum zzril delenit augue duis dolore te feugait nulla facilisi.</p>
</section>

<!-- footer -->
<footer class="abs footer">
  <div class="abs news">
    <svg class="abs" style="left:16px;top:20px" width="28" height="28" viewBox="0 0 28 28"><path d="M3 11l11-8 11 8v14H3z" fill="none" stroke="#85cae6" stroke-width="2"/><path d="M3 11l11 8 11-8" fill="none" stroke="#85cae6" stroke-width="2"/></svg>
    <span>Newsletter Signup</span>
    <div class="field">Enter your email here</div>
    <div class="sub">SUBSCRIBE</div>
  </div>
  <div class="abs follow">Follow Us</div>
  <div class="abs social" style="left:946px"></div>
  <div class="abs social" style="left:986px"></div>
  <div class="abs social" style="left:1026px"></div>
  <div class="abs social" style="left:1072px"></div>

  <!-- quick inquiry -->
  <svg class="abs" style="left:84px;top:162px" width="26" height="26" viewBox="0 0 26 26"><circle cx="13" cy="13" r="11" fill="none" stroke="#85cae6" stroke-width="2"/><text x="13" y="18" text-anchor="middle" font-size="14" fill="#85cae6" font-family="Bitter,serif">?</text></svg>
  <div class="abs f-title" style="left:122px;top:160px">Quick Inquiry</div>
  <div class="abs f-rule" style="left:84px;top:200px;width:472px"></div>
  <div class="abs input" style="left:84px;top:220px;width:226px">Name</div>
  <div class="abs input" style="left:84px;top:278px;width:226px">Email Address</div>
  <div class="abs input" style="left:84px;top:336px;width:226px">Phone Number</div>
  <div class="abs input" style="left:326px;top:220px;width:230px;height:96px">Message</div>
  <div class="abs submit" style="left:326px;top:336px;width:230px;height:40px">SUBMIT</div>

  <div class="abs vline" style="left:594px;top:196px;height:220px"></div>

  <!-- quick links -->
  <svg class="abs" style="left:626px;top:164px" width="20" height="24" viewBox="0 0 20 24"><rect x="2" y="3" width="16" height="19" fill="none" stroke="#85cae6" stroke-width="2"/><path d="M6 9h8M6 13h8M6 17h8" stroke="#85cae6" stroke-width="2"/></svg>
  <div class="abs f-title" style="left:658px;top:160px">Quick Links</div>
  <ul class="abs links" style="left:630px;top:212px">
    <li style="font-weight:700">Home</li><li>About Us</li><li>Our Products</li><li>Support</li><li>Faqs</li><li>Contact Us</li>
  </ul>

  <div class="abs vline" style="left:830px;top:196px;height:220px"></div>

  <!-- contact -->
  <svg class="abs" style="left:866px;top:164px" width="22" height="22" viewBox="0 0 22 22"><circle cx="11" cy="11" r="9" fill="none" stroke="#85cae6" stroke-width="2"/><path d="M2 11h18M11 2c-4 5-4 13 0 18M11 2c4 5 4 13 0 18" fill="none" stroke="#85cae6" stroke-width="1.5"/></svg>
  <div class="abs f-title" style="left:904px;top:160px">Contact Information</div>
  <div class="abs f-rule" style="left:866px;top:200px;width:268px"></div>
  <svg class="abs" style="left:870px;top:222px" width="14" height="18" viewBox="0 0 14 18"><path d="M7 17C2 10 1 8 1 6a6 6 0 0112 0c0 2-1 4-6 11z" fill="#fff"/><circle cx="7" cy="6" r="2" fill="#232323"/></svg>
  <div class="abs contact" style="left:894px;top:216px;width:240px">VENLOTIX,<br>Lorem ipsum dolor sit amet,<br>consec tetuer adipiscing elit, sed</div>
  <svg class="abs" style="left:870px;top:296px" width="16" height="16" viewBox="0 0 16 16"><path d="M3 1l3 3-2 2c1 2 3 4 6 6l2-2 3 3-2 2C7 15 1 9 1 3z" fill="#fff"/></svg>
  <div class="abs contact" style="left:898px;top:292px;font-weight:700">123-456-7890</div>
  <svg class="abs" style="left:870px;top:344px" width="16" height="12" viewBox="0 0 16 12"><rect width="16" height="12" fill="#fff"/><path d="M0 0l8 7 8-7" fill="none" stroke="#232323" stroke-width="1.5"/></svg>
  <div class="abs contact" style="left:898px;top:338px">info@venlotix.com</div>
</footer>

<div class="abs top-tab"></div>
<div class="abs bottom">Copyright 2016 <b>VENLOTIX</b> | All Right Reserved.</div>

</body>
</html>
```